Upscale business cards needed for Board of Directors

We need professional business cards created for members of our family business Board of Directors. We would like these relatively simple and straightforward, but also with a unique element to set them apart. Probably stick with neutral and simple colors - white, grey etc. We need space for the traditional elements, including name, title, address, email/phone number. And we will be creating several from this template so it needs to be template that is easy to switch information in and out of.
Business
See description

```html
<!DOCTYPE html>
<html lang="en">
<head>
<meta charset="utf-8">
<title>Keelstone Holdings – Business Cards</title>
<link rel="stylesheet" href="https://fonts.googleapis.com/css2?family=Arimo:wght@400;700&display=swap">
<style>
  :root {
    --page-bg: #e7e5e1;
    --card-white: #ffffff;
    --ink-dark: #2b2728;
    --ink-grey: #555152;
    --sand: #cbbf9c;
    --sand-light: #dcd3b7;
    --shadow: rgba(40, 32, 24, 0.22);
  }
  * { box-sizing: border-box; margin: 0; padding: 0; }
  html, body { width: 1200px; height: 902px; overflow: hidden; }
  body {
    background: var(--page-bg);
    font-family: "Arimo", Arial, sans-serif;
    position: relative;
  }
  .card {
    position: absolute;
    width: 540px;
    height: 310px;
    background: var(--card-white);
    border-radius: 3px;
    box-shadow: 0 10px 26px var(--shadow), 0 2px 4px var(--shadow);
    overflow: hidden;
  }
  .card--front { left: 100px; top: 110px; }
  .card--back { left: 560px; top: 482px; }

  .brand-name {
    position: absolute;
    font-weight: 700;
    color: var(--ink-dark);
    line-height: 1;
    white-space: nowrap;
  }
  .card--front .brand-name {
    left: 0; right: 0; top: 138px;
    text-align: center;
    font-size: 34px;
  }
  .card--back .brand-name {
    left: 34px; top: 56px;
    font-size: 24px;
  }

  .back-shape { position: absolute; inset: 0; }

  .person {
    position: absolute;
    left: 60px; top: 170px;
    color: var(--ink-grey);
  }
  .person__name { font-size: 20px; font-weight: 400; line-height: 1.05; }
  .person__title { font-size: 14px; font-weight: 400; color: var(--ink-dark); margin-left: 14px; }

  .contact {
    position: absolute;
    right: 22px; top: 138px;
    list-style: none;
    text-align: right;
    color: var(--ink-dark);
    font-size: 15px;
  }
  .contact__item {
    display: flex;
    justify-content: flex-end;
    align-items: center;
    gap: 9px;
    height: 22px;
    margin-bottom: 10px;
  }
  .contact__icon {
    width: 22px; height: 22px;
    background: var(--card-white);
    border-radius: 2px;
    display: flex; align-items: center; justify-content: center;
  }
  .contact__icon svg { width: 14px; height: 14px; fill: var(--ink-dark); }
</style>
</head>
<body>

  <section class="card card--front" aria-label="Card front">
    <p class="brand-name">Keelstone Holdings</p>
  </section>

  <section class="card card--back" aria-label="Card back">
    <svg class="back-shape" viewBox="0 0 540 310" preserveAspectRatio="none" aria-hidden="true">
      <defs>
        <linearGradient id="sandFill" x1="0" y1="0" x2="1" y2="1">
          <stop offset="0" stop-color="#cbbf9c"/>
          <stop offset="1" stop-color="#dcd3b7"/>
        </linearGradient>
      </defs>
      <path d="M314,0 L390,0 C355,125 262,240 160,310 C240,225 300,120 314,0 Z" fill="#2b2728"/>
      <path d="M390,0 L540,0 L540,310 L160,310 C262,240 355,125 390,0 Z" fill="url(#sandFill)"/>
    </svg>

    <p class="brand-name">Keelstone Holdings</p>

    <div class="person">
      <p class="person__name">Owen Carrow</p>
      <p class="person__title">Managing Director</p>
    </div>

    <ul class="contact">
      <li class="contact__item">
        <span>021-555-0142</span>
        <span class="contact__icon">
          <svg viewBox="0 0 24 24" aria-hidden="true"><path d="M6.6 10.8c1.4 2.8 3.8 5.1 6.6 6.6l2.2-2.2c.3-.3.7-.4 1-.2 1.1.4 2.3.6 3.6.6.6 0 1 .4 1 1V20c0 .6-.4 1-1 1C10.6 21 3 13.4 3 4c0-.6.4-1 1-1h3.5c.6 0 1 .4 1 1 0 1.3.2 2.5.6 3.6.1.3 0 .7-.2 1L6.6 10.8z"/></svg>
        </span>
      </li>
      <li class="contact__item">
        <span>keelstoneholdings@.com</span>
        <span class="contact__icon">
          <svg viewBox="0 0 24 24" aria-hidden="true"><path d="M2 5h20v14H2V5zm2 2v.4l8 5 8-5V7H4zm16 2.7-8 5-8-5V17h16V9.7z"/></svg>
        </span>
      </li>
      <li class="contact__item">
        <span>1180 N Linden Rd</span>
        <span class="contact__icon">
          <svg viewBox="0 0 24 24" aria-hidden="true"><path d="M12 2a7 7 0 0 0-7 7c0 5.2 7 13 7 13s7-7.8 7-13a7 7 0 0 0-7-7zm0 9.5A2.5 2.5 0 1 1 12 6.5a2.5 2.5 0 0 1 0 5z"/></svg>
        </span>
      </li>
    </ul>
  </section>

</body>
</html>
```